At Home Pet Euthanasia - business cards & brand stationary

We already have a logo and the colors and a website. Need a business card designed that will be able to customized to multiple veterinarians who will be partnering with us. The feel needs to be compassionate, comforting with our tagline 'A Gift of Love at Home'. It will be 2 sides.
On the back our platform/partner vets will be customizing each business card with their own service areas, phone numbers, name and title. On the front, i would like to see experimentation with use of our photos, the logo, tagline and a description 'Peaceful and Compassionate At-Home Pet Euthanasia'

```html
<!DOCTYPE html>
<html lang="en">
<head>
<meta charset="utf-8">
<title>Hearthway – Business Card</title>
<link rel="stylesheet" href="https://fonts.googleapis.com/css2?family=Montserrat:ital,wght@0,400;0,500;0,700;1,400&family=Fjalla+One&display=swap">
<style>
  :root {
    --brand-blue: #7597c0;
    --ink: #1d1d1f;
    --paper: #ffffff;
    --backdrop: #2e2e30;
    --watermark: #ececec;
    --photo-warm-a: #8a9a5a;
    --photo-warm-b: #d9d2c2;
    --photo-cool-a: #eef1f4;
    --photo-cool-b: #2a2a2c;
  }
  * { box-sizing: border-box; margin: 0; padding: 0; }
  html, body { width: 1200px; height: 866px; overflow: hidden; background: var(--backdrop); }
  body { font-family: "Montserrat", sans-serif; color: var(--ink); }
  .sheet {
    position: relative; width: 1200px; height: 866px;
    display: flex; flex-direction: column; align-items: center; justify-content: center; gap: 26px;
  }
  .card {
    position: relative; width: 700px; height: 400px; background: var(--paper);
    overflow: hidden; box-shadow: 0 10px 24px rgba(0,0,0,.45);
  }

  /* Front */
  .card-front .photo-row { position: absolute; inset: 0 0 88px 0; display: flex; }
  .photo { flex: 1; }
  .photo-white-dog { background: linear-gradient(150deg, var(--photo-warm-a) 0%, #b9a98a 45%, var(--photo-warm-b) 100%); }
  .photo-black-dog { background: linear-gradient(160deg, var(--photo-cool-a) 0%, #c9ced4 40%, #4a4c50 75%, var(--photo-cool-b) 100%); }
  .front-band {
    position: absolute; left: 0; right: 0; bottom: 0; height: 88px; background: var(--brand-blue);
    display: flex; align-items: center; justify-content: center;
  }
  .front-band .description {
    font-family: "Fjalla One", sans-serif; color: var(--paper); font-size: 27px; letter-spacing: .3px; text-transform: uppercase;
  }

  /* Back */
  .back-watermark {
    position: absolute; left: 70px; top: 20px; width: 230px; height: 230px;
    background: var(--watermark); opacity: .7;
  }
  .card-back .contact { position: absolute; left: 44px; top: 96px; width: 290px; }
  .contact .person-name { font-size: 23px; font-weight: 700; letter-spacing: 1.5px; color: var(--brand-blue); text-transform: uppercase; }
  .contact .person-title { font-size: 17px; margin-top: 2px; }
  .contact .rule { height: 1px; background: var(--brand-blue); margin: 12px 0 10px; }
  .contact .line { display: flex; align-items: center; gap: 8px; font-size: 16px; margin-top: 4px; }
  .contact svg { width: 15px; height: 15px; fill: var(--brand-blue); flex: none; }

  .brand { position: absolute; left: 372px; top: 150px; width: 300px; }
  .brand .wordmark { display: flex; align-items: center; gap: 12px; }
  .brand .mark { flex: none; width: 28px; height: 28px; border-radius: 50%; background: var(--brand-blue); }
  .brand .name { font-size: 42px; font-weight: 700; color: var(--brand-blue); letter-spacing: -.5px; white-space: nowrap; }
  .brand .tagline { font-size: 15px; font-style: italic; color: var(--brand-blue); margin: 2px 0 0 44px; }

  .address { position: absolute; right: 36px; top: 262px; width: 300px; text-align: right; font-size: 16px; line-height: 1.3; }
  .address .rule { height: 1px; background: var(--brand-blue); margin-top: 10px; }

  .back-base { position: absolute; left: 0; bottom: 0; width: 700px; height: 60px; }
  .website {
    position: absolute; right: 46px; bottom: 10px; font-size: 17px; color: var(--paper); letter-spacing: .5px;
  }
</style>
</head>
<body>
<main class="sheet">

  <section class="card card-front" aria-label="Card front">
    <div class="photo-row">
      <div class="photo photo-white-dog" role="img" aria-label="Photo of a white fluffy dog being held by its owner outdoors"></div>
      <div class="photo photo-black-dog" role="img" aria-label="Photo of an older black dog with a pale blue collar looking up"></div>
    </div>
    <div class="front-band">
      <p class="description">Peaceful and compassionate at-home pet euthanasia</p>
    </div>
  </section>

  <section class="card card-back" aria-label="Card back">
    <div class="back-watermark" aria-hidden="true"></div>

    <div class="contact">
      <p class="person-name">Daniel Reeves</p>
      <p class="person-title">Managing Director</p>
      <div class="rule"></div>
      <p class="line">
        <svg viewBox="0 0 24 24" aria-hidden="true"><path d="M6.6 10.8a15 15 0 0 0 6.6 6.6l2.2-2.2a1 1 0 0 1 1-.25 11.4 11.4 0 0 0 3.6.57 1 1 0 0 1 1 1V20a1 1 0 0 1-1 1A17 17 0 0 1 3 4a1 1 0 0 1 1-1h3.5a1 1 0 0 1 1 1c0 1.25.2 2.45.57 3.57a1 1 0 0 1-.25 1z"/></svg>
        044-555 010 204
      </p>
      <p class="line">
        <svg viewBox="0 0 24 24" aria-hidden="true"><path d="M2 5h20v14H2zm2 2v.4l8 5 8-5V7zm0 2.8V17h16V9.8l-8 5z"/></svg>
        hello@hearthwaypets.com
      </p>
    </div>

    <div class="brand">
      <div class="wordmark">
        <span class="mark" aria-hidden="true"></span>
        <span class="name">Hearthway</span>
      </div>
      <p class="tagline">A gift of love at home.</p>
    </div>

    <div class="address">
      <p>88, Willow Lane Cottages</p>
      <p>60718, Brookfield</p>
      <div class="rule"></div>
    </div>

    <svg class="back-base" viewBox="0 0 700 60" preserveAspectRatio="none" aria-hidden="true">
      <path d="M0 14 L330 46" stroke="var(--brand-blue)" stroke-width="3" fill="none"/>
      <path d="M0 24 L320 52" stroke="var(--brand-blue)" stroke-width="5" fill="none"/>
      <path d="M310 60 C330 30 345 22 380 22 L700 22 L700 60 Z" fill="var(--brand-blue)"/>
    </svg>
    <p class="website">www.hearthwaypets.com</p>
  </section>

</main>
</body>
</html>
```